PERI VALORE

We need a letterhead design for an Image & Etiquette Consultancy company based in Singapore.

The services we provide are Personal Image Consultation, Image & Etiquette Workshop for schools and corporate.

The design should have our corporate colour as seen in the logo files I have uploaded.

Since our company helps clients with their image, the design should be aesthetically very appealing. It should reflect a very classy & elegant feel.

I will print the letterhead using my printer but most of the time will use it to write letters to my clients therefore the format should include MS Word.

```html
<!DOCTYPE html>
<html lang="en">
<head>
<meta charset="utf-8">
<title>Peri Valore Letterhead</title>
<link rel="stylesheet" href="https://fonts.googleapis.com/css2?family=Questrial&family=Open+Sans:wght@400&display=swap">
<style>
  :root {
    --backdrop: #e3e3e1;
    --paper: #ffffff;
    --plum: #2f1c40;
    --gold: #b69a4c;
    --ink: #3a3a3a;
  }
  html, body {
    margin: 0;
    padding: 0;
    width: 1200px;
    height: 1200px;
    overflow: hidden;
    background: var(--backdrop);
  }
  .letterhead {
    position: absolute;
    left: 273px;
    top: 138px;
    width: 653px;
    height: 923px;
    background: var(--paper);
  }
  .brand {
    position: absolute;
    top: 62px;
    left: 0;
    width: 100%;
    display: flex;
    justify-content: center;
    align-items: center;
    gap: 12px;
  }
  .brand-mark {
    width: 10px;
    height: 10px;
    background: var(--gold);
  }
  .brand-name {
    font-family: "Questrial", sans-serif;
    font-size: 35px;
    letter-spacing: 1px;
    color: var(--plum);
    line-height: 1;
    margin: 0;
  }
  .header-rule {
    position: absolute;
    top: 120px;
    left: 50px;
    width: 553px;
    height: 2px;
    background: var(--plum);
  }
  .footer {
    position: absolute;
    top: 832px;
    left: 0;
    width: 100%;
    text-align: center;
  }
  .company-name {
    font-family: "Questrial", sans-serif;
    font-size: 15px;
    letter-spacing: 1px;
    color: var(--plum);
    margin: 0 0 8px;
  }
  .contact-line {
    font-family: "Open Sans", sans-serif;
    font-size: 9.5px;
    color: var(--ink);
    margin: 0 0 3px;
  }
</style>
</head>
<body>
  <main class="letterhead">
    <header class="brand">
      <span class="brand-mark"></span>
      <p class="brand-name">PERI VALORE</p>
    </header>
    <div class="header-rule"></div>
    <footer class="footer">
      <p class="company-name">Peri Valore Limited</p>
      <p class="contact-line">Your Long address with ode no. &nbsp;| &nbsp;your licence no.: xxx xxx xxx xx</p>
      <p class="contact-line">Phone: 000 000 000 | Email: yourname@perivalore.com | Website: www.perivalore.com</p>
    </footer>
  </main>
</body>
</html>
```